Maranoola Wines - web page for new Australian wine label

We need a landing page for our wine company. Maranoola is a family owned company, we grow the gapes, and make the wine in the Clare valley. Daniel Whitlock is the winemaker and is well known for his style, which is all about the fruit flavour rather than wood or age influences. Maranoola is Abriginal for 2 hills and a water source. We hand pick, hand plunge, foot crush resulting in elegant wine. Little to no additives, minimal filtering, single vineyard wines. Handcrafted with small releases of only the best fruit from carefully selected rows and bunches. The Clare valley is located two hours North of Adelaide, is known for cool climate and slow ripening, resulting in wines that have an elegant mouth feel, with bright colour and outstanding flavours. Our Brookmere vineyard has a Eastern aspect, gathering morning sun and escaping the hot afternoons, and in our opinion is on of the prettiest valleys in the world. Only 1000 cases per annum of the very best handpicked fruit, from the best rows. We hope you enjoy the Maranoola style, the reds are lighter in colour, fruit driven palate, more old world influence and the Riesling is on the dry side with fresh citrus. Minimal additives and filtering, our aim was to make wine with minimal influence from wine making. Handcrafted wines.

Target Market(s)

females 18 - 60 are the ones that buy 70 percent of wine, so whilst men are also a target, its the ladies we seek to appeal to.

Industry/Entity Type

It Company

Number of Pages Required

4 page

Font styles to use
Serif

Requirements
Must have
• Eye catching front page that makes me feel like i am ordering from quality company, that cares for what they do. Easy to use ordering, and delivery instructions.
• postage is $14.90 per case Australia wide.
• www.maranoolawines-example.com
Nice to have
• I want to see a fun and family oriented business that cares for the wine, we dont make a lot, its buckets and feet. But its wine made wanting to be the best in the world, we dont cut corners on quality. Handcrafted
Should not have
• dont really have any thoughts here, looking for all ideas

```html
<!DOCTYPE html>
<html lang="en">
<head>
<meta charset="utf-8">
<title>Maranoola Wines</title>
<link href="https://fonts.googleapis.com/css2?family=Lato:wght@300;400;700&display=swap" rel="stylesheet">
<style>
:root{
  --plum:#6b4577;
  --plum-deep:#5a3766;
  --plum-band:#684a72;
  --ink:#333333;
  --muted:#7a7a7a;
  --line:#444444;
  --white:#ffffff;
  --footer:#f4f4f4;
  --footer-line:#e2e2e2;
}
*{box-sizing:border-box;margin:0;padding:0}
html,body{width:1200px;height:2532px;overflow:hidden}
body{position:relative;background:var(--white);font-family:'Lato',sans-serif;color:var(--ink)}
.abs{position:absolute}

/* Hero */
.hero{position:absolute;left:0;top:0;width:1200px;height:621px;overflow:hidden}
.hero-photo{position:absolute;inset:0;
  background:
    radial-gradient(ellipse 230px 300px at 300px 280px,#4a3348 0%,#5b4057 45%,rgba(91,64,87,0) 100%),
    radial-gradient(ellipse 500px 400px at 850px 280px,#c79a3a 0%,rgba(199,154,58,0) 70%),
    linear-gradient(90deg,#3a2a22 0%,#6e5a2e 35%,#a98a3c 60%,#8a6a2a 85%,#5a4520 100%);}
.hero-shade{position:absolute;inset:0;background:linear-gradient(180deg,rgba(0,0,0,.25) 0%,rgba(0,0,0,.05) 40%,rgba(0,0,0,.15) 100%)}
.topbar{position:absolute;left:0;top:0;width:1200px;height:46px;background:rgba(30,20,20,.35);border-bottom:2px solid rgba(255,255,255,.85)}
.topbar .delivery{position:absolute;left:142px;top:13px;display:flex;align-items:center;gap:10px;color:var(--white);font-size:12px}
.topbar .tools{position:absolute;left:978px;top:13px;display:flex;gap:10px}
.mainnav{position:absolute;left:0;top:46px;width:1200px;height:67px;border-bottom:2px solid rgba(255,255,255,.85)}
.mainnav a{position:absolute;top:24px;color:var(--white);font-size:15px;text-decoration:none;letter-spacing:.3px}
.brand-nav{position:absolute;left:520px;top:18px;display:flex;align-items:center;gap:10px;color:var(--white);font-size:30px;font-weight:300}
.brand-dot{width:10px;height:10px;border-radius:50%;background:currentColor}
.hero-title{position:absolute;left:0;width:1200px;top:350px;text-align:center;color:var(--white);font-size:30px;font-weight:400}
.btn-ghost{position:absolute;border:2px solid var(--white);color:var(--white);font-size:14px;display:flex;align-items:center;justify-content:center;letter-spacing:.5px}
.hero-arrows{position:absolute;left:580px;top:544px;display:flex;gap:12px}

/* How it works */
.section-title{position:absolute;left:0;width:1200px;text-align:center;font-size:25px;font-weight:400;color:var(--ink)}
.step{position:absolute;top:753px;width:287px;height:300px;border:1.5px solid var(--line);text-align:center}
.step-icon{margin:28px auto 0;width:76px;height:76px;border-radius:10px;background:#ece3ef}
.step h3{margin-top:27px;font-size:17px;font-weight:400;letter-spacing:.3px}
.step p{margin:24px auto 0;width:230px;font-size:13.5px;line-height:24px;color:var(--muted)}

/* Feature band */
.band{position:absolute;left:0;top:1144px;width:1200px;height:539px;background:
  linear-gradient(90deg,#5e4266 0%,#6c4f76 50%,#5f4468 100%)}
.band-brand{position:absolute;left:145px;top:1270px;display:flex;align-items:center;gap:10px;color:var(--white);font-size:34px;font-weight:300}
.band-headline{position:absolute;left:145px;top:1355px;width:520px;color:var(--white);font-size:36px;font-weight:400;line-height:49px}
.band-photo{position:absolute;left:706px;top:1232px;width:302px;height:356px;
  background:linear-gradient(180deg,#9fc3e2 0%,#cfe0ea 40%,#e9e3d8 62%,#c9b7a6 100%)}

/* News */
.news{position:absolute;top:1852px;width:287px}
.news-photo{height:187px}
.news-date{margin-top:28px;font-size:11.5px;font-weight:700;color:var(--plum)}
.news p{margin-top:16px;font-size:13.5px;line-height:25px;color:var(--muted)}

/* Footer */
.footer{position:absolute;left:0;top:2228px;width:1200px;height:245px;background:var(--footer)}
.footer-brand{position:absolute;left:142px;top:2275px;display:flex;align-items:center;gap:8px;color:var(--plum);font-size:28px;font-weight:300}
.socials{position:absolute;left:172px;top:2330px;display:flex;gap:6px}
.socials span{width:18px;height:18px;border:1.3px solid #666;border-radius:50%}
.footer-links{position:absolute;list-style:none;font-size:11.5px;line-height:24px;color:var(--ink)}
.newsletter-title{position:absolute;left:766px;top:2280px;font-size:15px;color:var(--ink)}
.newsletter-input{position:absolute;left:766px;top:2316px;width:287px;height:44px;background:var(--white);font-size:9px;color:#aaa;padding:17px 0 0 12px;letter-spacing:.3px}
.newsletter-btn{position:absolute;left:766px;top:2372px;width:151px;height:38px;background:var(--plum);color:var(--white);font-size:11px;font-weight:700;display:flex;align-items:center;justify-content:center}
.bottombar{position:absolute;left:0;top:2473px;width:1200px;height:59px;border-top:1px solid var(--footer-line);background:var(--white);text-align:center;font-size:11px;padding-top:22px;color:var(--ink)}
</style>
</head>
<body>

<header class="hero">
  <div class="hero-photo" role="img" aria-label="Close-up photo of a ripe bunch of dark grapes on the vine in warm sunlight"></div>
  <div class="hero-shade"></div>
  <div class="topbar">
    <div class="delivery">
      <svg width="14" height="14" viewBox="0 0 14 14" fill="none" stroke="#fff" stroke-width="1.4"><rect x="1" y="2" width="12" height="11"/><line x1="1" y1="5.5" x2="13" y2="5.5"/><line x1="4" y1="0.5" x2="4" y2="3"/><line x1="10" y1="0.5" x2="10" y2="3"/></svg>
      Delivery charge is $14.90 per case Australia wide
    </div>
    <div class="tools">
      <svg width="18" height="18" viewBox="0 0 18 18" fill="none" stroke="#8a5a9a" stroke-width="1.5"><rect x="3" y="5" width="12" height="10" rx="1"/><path d="M6 5a3 3 0 0 1 6 0"/></svg>
      <svg width="18" height="18" viewBox="0 0 18 18" fill="none" stroke="#fff" stroke-width="1.4"><circle cx="9" cy="9" r="7"/><ellipse cx="9" cy="9" rx="3" ry="7"/><line x1="2" y1="9" x2="16" y2="9"/></svg>
      <svg width="18" height="18" viewBox="0 0 18 18" fill="none" stroke="#fff" stroke-width="1.6"><circle cx="10.5" cy="7.5" r="5"/><line x1="7" y1="11" x2="2" y2="16"/></svg>
    </div>
  </div>
  <nav class="mainnav">
    <a style="left:196px">HOME</a>
    <a style="left:279px">ABOUT US</a>
    <a style="left:388px">SERVICES</a>
    <div class="brand-nav"><span class="brand-dot"></span>Maranoola</div>
    <a style="left:744px">FAQ'S</a>
    <a style="left:824px">TESTIMONIALS</a>
    <a style="left:964px">CONTACT US</a>
  </nav>
  <h1 class="hero-title">A Family Owned Wine Company</h1>
  <div class="btn-ghost" style="left:522px;top:414px;width:157px;height:43px">SHOP NOW</div>
  <div class="hero-arrows">
    <svg width="12" height="16" viewBox="0 0 12 16" fill="none" stroke="#fff" stroke-width="2"><polyline points="9,2 3,8 9,14"/></svg>
    <svg width="12" height="16" viewBox="0 0 12 16" fill="none" stroke="#fff" stroke-width="2"><polyline points="3,2 9,8 3,14"/></svg>
  </div>
</header>

<h2 class="section-title" style="top:680px">HOW IT WORKS</h2>
<div class="step" style="left:142px">
  <div class="step-icon" role="img" aria-label="Line icon of a hand picking"></div>
  <h3>WE HAND PICK</h3>
  <p>Neque porro quisquam est qui dolorem ipsum quia dolor sit amet, consectetur, adipisci velit...</p>
</div>
<div class="step" style="left:454px">
  <div class="step-icon" role="img" aria-label="Line icon of two hands plunging"></div>
  <h3>HAND PLUNGE</h3>
  <p>Neque porro quisquam est qui dolorem ipsum quia dolor sit amet, consectetur, adipisci velit...</p>
</div>
<div class="step" style="left:768px">
  <div class="step-icon" role="img" aria-label="Line icon of a bare foot"></div>
  <h3>FOOT CRUSH RESULTING</h3>
  <p>Neque porro quisquam est qui dolorem ipsum quia dolor sit amet, consectetur, adipisci velit...</p>
</div>

<section class="band" role="img" aria-label="Winery cellar photo with machinery under a purple tint"></section>
<div class="band-brand"><span class="brand-dot"></span>Maranoola</div>
<p class="band-headline">Only 1000 cases per annum of the very best handpicked fruit, from the best rows.</p>
<div class="btn-ghost" style="left:150px;top:1536px;width:157px;height:44px">SHOP NOW</div>
<svg class="abs" style="left:329px;top:1552px" width="176" height="44" viewBox="0 0 176 44" fill="none" stroke="#fff" stroke-width="3" stroke-linecap="round"><path d="M3 22 C50 44 120 40 168 16"/><polyline points="150,8 168,16 158,32"/></svg>
<div class="band-photo" role="img" aria-label="Photo of a bottle of white wine beside a bowl of lobster on a sunny beach"></div>

<h2 class="section-title" style="top:1756px">LATEST NEWS</h2>
<article class="news" style="left:142px">
  <div class="news-photo" role="img" aria-label="Photo of a family group celebrating in the vineyard" style="background:linear-gradient(180deg,#8fa9c6 0%,#7a8a5a 45%,#6a6248 100%)"></div>
  <div class="news-date">FEBRUARY 24th | 2017</div>
  <p>Neque porro quisquam est qui dolorem ipsum quia dolor sit amet, consectetur.</p>
</article>
<article class="news" style="left:454px">
  <div class="news-photo" role="img" aria-label="Photo of dark grape bunches among vine leaves" style="background:linear-gradient(160deg,#4f6a3a 0%,#3b3a45 50%,#5a7a40 100%)"></div>
  <div class="news-date">FEBRUARY 24th | 2017</div>
  <p>Neque porro quisquam est qui dolorem ipsum quia dolor sit amet, consectetur.</p>
</article>
<article class="news" style="left:768px">
  <div class="news-photo" role="img" aria-label="Photo of winemakers working at steel tanks in the winery" style="background:linear-gradient(180deg,#c9c3c8 0%,#8c8890 50%,#5f5a60 100%)"></div>
  <div class="news-date">FEBRUARY 24th | 2017</div>
  <p>Neque porro quisquam est qui dolorem ipsum quia dolor sit amet, consectetur..</p>
</article>

<footer class="footer"></footer>
<div class="footer-brand"><span class="brand-dot"></span>Maranoola</div>
<div class="socials"><span></span><span></span><span></span><span></span></div>
<ul class="footer-links" style="left:361px;top:2277px">
  <li>HOME</li><li>ABOUT US</li><li>SERVICES</li><li>FAQ'S</li><li>TESTIMONIALS</li><li>CONTACT US</li>
</ul>
<ul class="footer-links" style="left:562px;top:2277px">
  <li>TERMS OF SERVICE</li><li>PRIVACY POLICY</li><li>HELP</li><li>DISCLAIMER</li>
</ul>
<div class="newsletter-title">NEWSLETTER SIGN UP</div>
<div class="newsletter-input">ENTER YOUR E-MAIL ADDRESS</div>
<div class="newsletter-btn">SUBSCRIBE NOW</div>
<div class="bottombar">© 2017 COMPANY NAME &nbsp;| ALL RIGHTS RESERVED</div>

</body>
</html>
```